Business Card for a Dental Office

The design should communicate integrity, quality and reliability. We also want the card look elegant, simple, but still stand out, different from the traditional-dental-office business card.

Industry/Entity Type

Business

```html
<!DOCTYPE html>
<html lang="en">
<head>
<meta charset="utf-8">
<title>Marlow Dental Centre – Business Card</title>
<link rel="stylesheet" href="https://fonts.googleapis.com/css2?family=Oswald:wght@500;600&family=Open+Sans:wght@400;600&display=swap">
<style>
  :root {
    --backdrop: #e9e4dc;
    --card: #fbfbf9;
    --ink: #141414;
    --gold: #c9b04a;
    --muted: #3a3a3a;
  }
  html, body {
    margin: 0;
    width: 1200px;
    height: 1022px;
    overflow: hidden;
    background: var(--backdrop);
  }
  .stage {
    width: 1200px;
    height: 1022px;
    display: flex;
    align-items: center;
    justify-content: center;
  }
  .card {
    position: relative;
    width: 900px;
    height: 514px;
    background: var(--card);
    border-radius: 18px;
    box-shadow: 0 14px 40px rgba(60, 50, 30, 0.18);
    overflow: hidden;
  }
  .brand {
    position: absolute;
    left: 90px;
    top: 110px;
    display: flex;
    align-items: center;
    gap: 24px;
  }
  .brand-mark {
    width: 96px;
    height: 96px;
    background: var(--gold);
    flex: none;
  }
  .brand-text { display: flex; flex-direction: column; }
  .brand-name {
    font-family: "Oswald", sans-serif;
    font-weight: 600;
    font-size: 56px;
    line-height: 1;
    color: var(--ink);
    text-transform: uppercase;
    letter-spacing: 0.5px;
    white-space: nowrap;
  }
  .tagline {
    margin-top: 8px;
    font-family: "Open Sans", sans-serif;
    font-weight: 600;
    font-size: 22px;
    color: var(--gold);
    text-transform: uppercase;
    letter-spacing: 1px;
    white-space: nowrap;
  }
  .contact-row {
    position: absolute;
    left: 0;
    right: 0;
    top: 312px;
    display: flex;
    justify-content: center;
    align-items: center;
  }
  .person {
    text-align: right;
    padding-right: 26px;
  }
  .person-name {
    font-family: "Open Sans", sans-serif;
    font-weight: 600;
    font-size: 38px;
    color: var(--ink);
    text-transform: uppercase;
    line-height: 1.1;
    white-space: nowrap;
  }
  .person-role {
    font-family: "Open Sans", sans-serif;
    font-size: 22px;
    color: var(--gold);
    text-transform: uppercase;
    letter-spacing: 1px;
  }
  .divider {
    width: 2px;
    height: 110px;
    background: var(--ink);
  }
  .details {
    list-style: none;
    margin: 0;
    padding: 0 0 0 26px;
    font-family: "Open Sans", sans-serif;
    font-size: 21px;
    color: var(--muted);
    line-height: 1.5;
    white-space: nowrap;
  }
  .details li { display: flex; align-items: center; gap: 12px; }
  .details svg { width: 18px; height: 18px; flex: none; }
  .icon-stroke { fill: none; stroke: var(--gold); stroke-width: 2; }
</style>
</head>
<body>
<main class="stage">
  <article class="card">
    <header class="brand">
      <div class="brand-mark"></div>
      <div class="brand-text">
        <div class="brand-name">Marlow Dental Centre</div>
        <div class="tagline">Calm care for every single smile</div>
      </div>
    </header>

    <section class="contact-row">
      <div class="person">
        <div class="person-name">Evan Hale</div>
        <div class="person-role">Director</div>
      </div>
      <div class="divider"></div>
      <ul class="details">
        <li>
          <svg viewBox="0 0 20 20"><path fill="var(--gold)" d="M5 2l3 4-2 2c1 2.5 3.5 5 6 6l2-2 4 3-2 3C9 18 2 11 2 4z"/></svg>
          +1 555 014-2290
        </li>
        <li>
          <svg viewBox="0 0 20 20"><rect class="icon-stroke" x="2" y="4" width="16" height="12" rx="1"/><path class="icon-stroke" d="M2 5l8 6 8-6"/></svg>
          info@marlowdentalcentre.com
        </li>
        <li>
          <svg viewBox="0 0 20 20"><circle class="icon-stroke" cx="10" cy="10" r="8"/><path class="icon-stroke" d="M2 10h16M10 2c3 3 3 13 0 16M10 2c-3 3-3 13 0 16"/></svg>
          www.marlowdentalcentre.com
        </li>
      </ul>
    </section>
  </article>
</main>
</body>
</html>
```